Harborlane Products Flyer

Harborlane Lending Group, Inc.
Licensed Mortgage Company
Serving the DMV since 1997
"You open the Harborlane, we'll carry the load"
We specialize in...
FHA Loans
* Credit Scores as low as 500
* 203K Renovation Loans
Conventional Loans
* As little as 1% Down
* Bank Statement for Self-Employed
Investor Loans
* DSCR, & Fix & Flip
* Commercial & New Construction
Other Programs
* HELOCS & Reverse Mortgages
Call today for a free consultation
(800) 914-6027
www.harborlanehomeloans.com
NMLS #731860

```html
<!DOCTYPE html>
<html lang="en">
<head>
<meta charset="utf-8">
<title>Harborlane Products Flyer</title>
<link href="https://fonts.googleapis.com/css2?family=Bebas+Neue&family=Poppins:wght@400;600;700&display=swap" rel="stylesheet">
<style>
  :root {
    --blue: #1f5878;
    --blue-deep: #194a66;
    --gold: #b7a644;
    --paper: #ffffff;
    --stage: #e6e7e9;
    --ink: #1d1d1d;
  }
  * { box-sizing: border-box; margin: 0; padding: 0; }
  html, body { width: 1200px; height: 789px; overflow: hidden; }
  body { background: var(--stage); font-family: "Poppins", sans-serif; }
  .flyer {
    position: absolute; left: 300px; top: 6px;
    width: 600px; height: 776px; background: var(--paper); overflow: hidden;
  }
  .brand { position: absolute; left: 40px; top: 28px; display: flex; align-items: center; gap: 10px; }
  .brand-dot { width: 26px; height: 26px; border-radius: 50%; background: var(--gold); }
  .brand-name { font-weight: 700; font-size: 20px; color: var(--blue); }
  .photo {
    position: absolute; left: 0; top: 82px; width: 600px; height: 316px;
    background: linear-gradient(135deg, #efeeec 0%, #e2ddd7 40%, #b48b6c 60%, #ebe8e4 100%);
  }
  .photo-rule { position: absolute; left: 0; top: 398px; width: 600px; height: 6px; background: var(--blue); }
  .nmls {
    position: absolute; left: 380px; top: 62px; width: 180px; height: 40px;
    background: var(--blue); color: #fff; font-size: 17px;
    display: flex; align-items: center; justify-content: center;
  }
  .served { position: absolute; left: 380px; top: 106px; width: 180px; text-align: center; font-weight: 700; font-size: 12px; line-height: 1.3; color: var(--blue); }
  .served span { display: block; color: var(--gold); }
  .served-bg { position: absolute; left: 372px; top: 100px; width: 196px; height: 44px; background: var(--paper); }
  .services { position: absolute; left: 370px; top: 160px; width: 190px; }
  .service {
    height: 132px; color: #fff; text-align: center;
    display: flex; flex-direction: column; align-items: center; justify-content: center;
    padding: 0 10px;
  }
  .service.blue { background: var(--blue); }
  .service.gold { background: var(--gold); }
  .service svg { margin-bottom: 8px; }
  .service h3 { font-weight: 700; font-size: 15px; margin-bottom: 3px; }
  .service.gold h3 { color: var(--blue-deep); }
  .service p { font-size: 11.5px; line-height: 1.3; }
  .headline { position: absolute; left: 36px; top: 420px; font-family: "Bebas Neue", sans-serif; line-height: 0.9; }
  .headline .lead { font-size: 50px; color: var(--blue); display: block; }
  .headline .name { font-size: 70px; color: var(--gold); display: block; }
  .headline .tail { font-size: 34px; color: var(--blue); display: block; margin-top: 4px; }
  .call {
    position: absolute; left: 0; top: 578px; width: 262px; height: 50px;
    background: var(--blue); color: #fff; padding: 6px 0 0 36px; line-height: 1.25;
  }
  .call strong { font-size: 15px; display: block; }
  .call span { font-size: 13px; font-weight: 600; }
  .phone { position: absolute; left: 36px; top: 640px; display: flex; align-items: center; gap: 10px; font-weight: 700; font-size: 20px; color: var(--ink); }
  .footer-rule { position: absolute; left: 0; top: 682px; width: 600px; height: 3px; background: var(--gold); }
  .footer { position: absolute; left: 0; top: 685px; width: 600px; height: 91px; background: var(--blue); color: #fff; font-size: 9.5px; }
  .foot-item { position: absolute; display: flex; align-items: center; gap: 8px; }
  .foot-item.address { left: 36px; top: 14px; line-height: 1.35; }
  .foot-item.web { left: 36px; top: 56px; }
  .foot-item.tel { left: 400px; top: 56px; }
  .icon-dot { width: 18px; height: 18px; border-radius: 50%; background: var(--gold); display: flex; align-items: center; justify-content: center; flex: none; }
  .services-overlap { position: absolute; left: 370px; top: 688px; width: 190px; height: 4px; background: var(--gold); }
</style>
</head>
<body>
<main class="flyer">
  <div class="brand">
    <div class="brand-dot"></div>
    <div class="brand-name">Harborlane Lending Group, Inc.</div>
  </div>

  <div class="photo" role="img" aria-label="Smiling family of four relaxing together on a white bed"></div>
  <div class="photo-rule"></div>

  <div class="nmls">NMLS #731860</div>
  <div class="served-bg"></div>
  <div class="served">Serving the DMV<span>Since 1997</span></div>

  <section class="services">
    <div class="service blue">
      <svg width="34" height="34" viewBox="0 0 34 34"><circle cx="17" cy="17" r="17" fill="#b7a644"/><path d="M9 18 L17 11 L25 18 M11 17 V24 H23 V17" fill="none" stroke="#fff" stroke-width="1.6"/></svg>
      <h3>FHA Loans</h3>
      <p>Credit Scores as low as 500<br>203K Renovation Loans</p>
    </div>
    <div class="service gold">
      <svg width="34" height="34" viewBox="0 0 34 34"><circle cx="17" cy="17" r="17" fill="#1f5878"/><rect x="11" y="9" width="12" height="16" fill="none" stroke="#fff" stroke-width="1.6"/><path d="M14 14 H20 M14 18 H20 M14 22 H18" stroke="#fff" stroke-width="1.4"/></svg>
      <h3>Conventional Loans</h3>
      <p>As little as 1% Down<br>Bank Statement for Self Employed</p>
    </div>
    <div class="service blue">
      <svg width="34" height="34" viewBox="0 0 34 34"><circle cx="17" cy="17" r="17" fill="#b7a644"/><circle cx="17" cy="13" r="4" fill="none" stroke="#fff" stroke-width="1.6"/><path d="M10 25 C10 19 24 19 24 25" fill="none" stroke="#fff" stroke-width="1.6"/></svg>
      <h3>Investor Loans</h3>
      <p>DSCR, &amp; Fix &amp; Flip<br>Commercial &amp; New Construction</p>
    </div>
    <div class="service gold">
      <svg width="34" height="34" viewBox="0 0 34 34"><circle cx="17" cy="17" r="17" fill="#1f5878"/><rect x="9" y="11" width="16" height="12" fill="none" stroke="#fff" stroke-width="1.6"/><path d="M12 15 H22 M12 19 H18" stroke="#fff" stroke-width="1.4"/></svg>
      <h3>Other Programs</h3>
      <p>HELOCS &amp; Reverse<br>Mortgages</p>
    </div>
  </section>

  <h1 class="headline">
    <span class="lead">You open the</span>
    <span class="name">Harborlane</span>
    <span class="tail">We'll carry the load</span>
  </h1>

  <div class="call"><strong>Call Today</strong><span>for a Free Consultation</span></div>
  <div class="phone">
    <svg width="16" height="16" viewBox="0 0 24 24"><path d="M6.6 10.8a15.1 15.1 0 0 0 6.6 6.6l2.2-2.2c.3-.3.7-.4 1-.2 1.1.4 2.3.6 3.6.6.6 0 1 .4 1 1V20c0 .6-.4 1-1 1A17 17 0 0 1 3 4c0-.6.4-1 1-1h3.5c.6 0 1 .4 1 1 0 1.3.2 2.5.6 3.6.1.3 0 .7-.2 1z" fill="#b7a644"/></svg>
    (800) 914-6027
  </div>

  <div class="footer-rule"></div>
  <footer class="footer">
    <div class="foot-item address">
      <span class="icon-dot"><svg width="10" height="10" viewBox="0 0 24 24"><path d="M12 2a7 7 0 0 0-7 7c0 5 7 13 7 13s7-8 7-13a7 7 0 0 0-7-7zm0 9.5A2.5 2.5 0 1 1 12 6.5a2.5 2.5 0 0 1 0 5z" fill="#1f5878"/></svg></span>
      <span>MARYLAND OFFICE: 2200<br>Tidewater Rd, Columbia, MD 21044</span>
    </div>
    <div class="foot-item web">
      <span class="icon-dot"><svg width="10" height="10" viewBox="0 0 24 24"><circle cx="12" cy="12" r="9" fill="none" stroke="#1f5878" stroke-width="2"/><path d="M3 12h18M12 3c3 3 3 15 0 18M12 3c-3 3-3 15 0 18" fill="none" stroke="#1f5878" stroke-width="1.6"/></svg></span>
      <span>www.harborlanehomeloans.com</span>
    </div>
    <div class="foot-item tel">
      <span class="icon-dot"><svg width="10" height="10" viewBox="0 0 24 24"><path d="M6.6 10.8a15.1 15.1 0 0 0 6.6 6.6l2.2-2.2c.3-.3.7-.4 1-.2 1.1.4 2.3.6 3.6.6.6 0 1 .4 1 1V20c0 .6-.4 1-1 1A17 17 0 0 1 3 4c0-.6.4-1 1-1h3.5c.6 0 1 .4 1 1 0 1.3.2 2.5.6 3.6.1.3 0 .7-.2 1z" fill="#1f5878"/></svg></span>
      <span>(800) 914-6027</span>
    </div>
  </footer>
</main>
</body>
</html>
```